Northfield Builders Guild Business card

We are looking for a new business card design with photo included.
Our business is a nonprofit construction contractor membership organization. We offer business education, assist with business setup and licensing, provide safety training, and provide a member directory.
URL: www.builderslinkguild.org
Color code:
CMYK: 0 cyan, 42 magenta, 100 yellow, 0 black for Print.
Hexidecimal: #FF9900
RGB: R 255; G 153; B 0

```html
<!DOCTYPE html>
<html lang="en">
<head>
<meta charset="utf-8">
<title>Northfield Builders Guild — Business Card</title>
<link href="https://fonts.googleapis.com/css2?family=Montserrat:wght@400;500;800&display=swap" rel="stylesheet">
<style>
  :root {
    --orange: #f7962a;
    --ink: #3a3a3c;
    --paper: #ffffff;
    --backdrop: #e4e4e4;
    --rule: #8a8a8a;
  }
  * { margin: 0; padding: 0; box-sizing: border-box; }
  html, body { width: 1200px; height: 1200px; overflow: hidden; }
  body {
    background: var(--backdrop);
    font-family: "Montserrat", Arial, sans-serif;
    position: relative;
  }
  .card {
    position: absolute;
    left: 262px;
    width: 686px;
    height: 392px;
    border-radius: 22px;
    overflow: hidden;
    box-shadow: 0 18px 30px rgba(0,0,0,0.22);
  }
  .card--front { top: 165px; background: var(--paper); }
  .card--back { top: 653px; background: var(--orange); }

  .front__band {
    position: absolute; left: 0; right: 0; bottom: 0;
    height: 14px; background: var(--orange);
  }
  .wordmark {
    font-weight: 800;
    text-align: center;
    line-height: 1.05;
    letter-spacing: 0.5px;
  }
  .front__wordmark {
    position: absolute; left: 72px; width: 270px; top: 155px;
    font-size: 29px; color: var(--ink);
  }
  .front__divider {
    position: absolute; left: 358px; top: 88px;
    width: 1px; height: 215px; background: var(--rule);
  }
  .details {
    position: absolute; left: 385px; top: 88px;
    color: var(--ink);
  }
  .details__name { font-size: 23px; font-weight: 500; letter-spacing: 0.6px; }
  .details__title { font-size: 16px; color: var(--orange); margin-top: 1px; }
  .details__address { font-size: 16px; line-height: 20px; margin-top: 14px; }
  .contact { list-style: none; margin-top: 12px; font-size: 16px; line-height: 20px; }
  .contact li { display: flex; align-items: center; gap: 8px; }
  .contact svg { width: 14px; height: 14px; fill: var(--orange); flex: none; }

  .back__wordmark {
    position: absolute; left: 0; right: 0; top: 130px;
    font-size: 46px; color: var(--ink);
  }
  .back__url {
    position: absolute; left: 0; right: 0; top: 325px;
    text-align: center; color: var(--paper);
    font-size: 15px; letter-spacing: 3.5px;
  }
</style>
</head>
<body>
  <section class="card card--front">
    <div class="wordmark front__wordmark">NORTHFIELD<br>BUILDERS GUILD</div>
    <div class="front__divider"></div>
    <div class="details">
      <div class="details__name">DANIEL HARPER</div>
      <div class="details__title">President</div>
      <div class="details__address">2450 Ridgeway Ave.,<br>Suite #200<br>Millbrook, OR 97301</div>
      <ul class="contact">
        <li><svg viewBox="0 0 24 24"><path d="M6.6 10.8a15.2 15.2 0 0 0 6.6 6.6l2.2-2.2c.3-.3.7-.4 1-.2 1.1.4 2.3.6 3.6.6.6 0 1 .4 1 1V20c0 .6-.4 1-1 1A17 17 0 0 1 3 4c0-.6.4-1 1-1h3.5c.6 0 1 .4 1 1 0 1.3.2 2.5.6 3.6.1.3 0 .7-.2 1z"/></svg>(555) 210-4837</li>
        <li><svg viewBox="0 0 24 24"><path d="M7 1h10a2 2 0 0 1 2 2v18a2 2 0 0 1-2 2H7a2 2 0 0 1-2-2V3a2 2 0 0 1 2-2zm0 3v14h10V4z"/></svg>555.318.0926</li>
        <li><svg viewBox="0 0 24 24"><path d="M2 5h20v14H2zm2 2v.5l8 5 8-5V7l-8 5z"/></svg>support@nbguild.org</li>
        <li><svg viewBox="0 0 24 24"><circle cx="12" cy="12" r="10"/></svg>builderslinkguild.org</li>
      </ul>
    </div>
    <div class="front__band"></div>
  </section>

  <section class="card card--back">
    <div class="wordmark back__wordmark">NORTHFIELD<br>BUILDERS GUILD</div>
    <div class="back__url">www.builderslinkguild.org</div>
  </section>
</body>
</html>
```